Communication and Marketing agency needs a new presentation card

We are a group of communication and marketing agencies specialized in companies that are in the logistics and industrial sector. The head agency is TELVANO Grupo and the group consists of 4 agencies: TELVANO Media, TELVANO Digital, TELVANO Research and DifundeEnPantalla. We hace 4 offices in Spain (Madrid, Barcelona, Valencia and Murcia). We are looking for a clean and attractive design that transmits our experience, brand presence in the market and knowledge to those who receive the card.It has to maintain the colors of the logo that is attached.
Target Market(s)
logistics and industrial sector
Marketing department
Contact Information for Business Card
Clean and attractive design

```html
<!DOCTYPE html>
<html lang="es">
<head>
<meta charset="utf-8">
<title>TELVANO Grupo – Tarjeta de presentación</title>
<link href="https://fonts.googleapis.com/css2?family=Montserrat:wght@300;400;500;600&display=swap" rel="stylesheet">
<style>
  :root {
    --bg: #161616;
    --card: #262626;
    --card-edge: #2e2e2e;
    --red: #c8102e;
    --white: #f4f4f4;
    --grey: #cfcfcf;
    --emboss: #161616;
    --emboss-light: rgba(255,255,255,.12);
    --silver: #d9d9d9;
    --map-light: #e8e8e8;
    --map-dark: #8a8a8a;
  }
  * { box-sizing: border-box; margin: 0; padding: 0; }
  html, body { width: 1200px; height: 900px; overflow: hidden; }
  body {
    background: var(--bg);
    font-family: "Montserrat", sans-serif;
    position: relative;
  }
  .card {
    position: absolute;
    left: 280px;
    width: 640px;
    height: 390px;
    background: linear-gradient(135deg, var(--card-edge), var(--card) 60%, #202020);
    box-shadow: 0 10px 30px rgba(0,0,0,.55);
  }
  .card--back { top: 30px; }
  .card--front { top: 480px; }

  /* Back: group brands */
  .brand {
    position: absolute;
    font-weight: 300;
    letter-spacing: 2px;
    line-height: 1;
    text-align: right;
  }
  .brand__name { display: block; font-size: 30px; }
  .brand__unit { display: block; font-size: 17px; font-weight: 400; letter-spacing: 1px; margin-top: 5px; }
  .brand--embossed { color: var(--emboss); text-shadow: 0 1px 0 var(--emboss-light), 0 -1px 0 rgba(0,0,0,.5); }
  .brand--silver { color: var(--silver); }
  .brand--media { left: 90px; top: 110px; }
  .brand--digital { left: 90px; top: 195px; }
  .brand--research { left: 330px; top: 120px; }
  .brand--video { left: 330px; top: 215px; font-size: 26px; text-align: left; }

  /* Front */
  .map {
    position: absolute;
    left: 50px; top: 40px;
    width: 290px; height: 230px;
    background: radial-gradient(ellipse at 45% 50%, var(--map-light) 0%, var(--map-dark) 55%, transparent 72%);
    opacity: .55;
  }
  .offices {
    position: absolute;
    left: 36px; top: 302px;
    font-size: 15px; font-weight: 600;
    color: var(--white);
    white-space: nowrap;
  }
  .divider { position: absolute; left: 360px; width: 2px; }
  .divider--red { top: 40px; height: 130px; background: var(--red); }
  .divider--white { top: 170px; height: 180px; background: var(--white); }

  .contact { position: absolute; left: 390px; top: 50px; }
  .contact__brand {
    color: var(--red);
    font-size: 30px; font-weight: 300;
    letter-spacing: 2px; line-height: 1.1;
  }
  .contact__name { margin-top: 22px; color: var(--red); font-size: 21px; font-weight: 600; letter-spacing: 1px; }
  .contact__role { color: var(--grey); font-size: 14px; font-weight: 400; letter-spacing: 1px; margin-top: 2px; }
  .contact__list { list-style: none; margin-top: 18px; }
  .contact__item {
    display: flex; align-items: center; gap: 10px;
    color: var(--white); font-size: 15px; letter-spacing: 1px;
    margin-bottom: 8px;
  }
  .contact__icon { width: 12px; height: 12px; flex: none; }
  .contact__dot { width: 9px; height: 9px; border-radius: 50%; background: var(--red); margin: 0 2px 0 1px; flex: none; }
</style>
</head>
<body>

<section class="card card--back" aria-label="Reverso: agencias del grupo">
  <div class="brand brand--embossed brand--media"><span class="brand__name">TELVANO</span><span class="brand__unit">Media</span></div>
  <div class="brand brand--embossed brand--digital"><span class="brand__name">TELVANO</span><span class="brand__unit">Digital</span></div>
  <div class="brand brand--silver brand--research"><span class="brand__name">TELVANO</span><span class="brand__unit">Research</span></div>
  <div class="brand brand--silver brand--video">DifundeEnPantalla</div>
</section>

<section class="card card--front" aria-label="Anverso: datos de contacto">
  <div class="map" role="img" aria-label="Mapa punteado de España con marcadores rojos en Madrid, Barcelona, Valencia y Murcia"></div>
  <p class="offices">Madrid | Barcelona | Valencia | Murcia</p>

  <span class="divider divider--red"></span>
  <span class="divider divider--white"></span>

  <div class="contact">
    <div class="contact__brand">TELVANO Grupo</div>
    <div class="contact__name">Adrián Solera</div>
    <div class="contact__role">Director</div>
    <ul class="contact__list">
      <li class="contact__item">
        <svg class="contact__icon" viewBox="0 0 12 12"><path d="M2.5 1l2 2.2-1 1.3c.8 1.6 2 2.8 3.5 3.5l1.3-1 2.2 2-1.2 1.8C5 10.5 1.5 7 .7 2.2z" fill="#c8102e"/></svg>
        910 472 385
      </li>
      <li class="contact__item">
        <svg class="contact__icon" viewBox="0 0 12 12"><rect x="3" y="0.5" width="6" height="11" rx="1" fill="none" stroke="#c8102e" stroke-width="1.2"/><circle cx="6" cy="9.5" r=".7" fill="#c8102e"/></svg>
        655 218 473
      </li>
      <li class="contact__item">
        <svg class="contact__icon" viewBox="0 0 12 12"><rect x=".6" y="2.5" width="10.8" height="7" fill="none" stroke="#c8102e" stroke-width="1.1"/><path d="M.6 2.5L6 6.5l5.4-4" fill="none" stroke="#c8102e" stroke-width="1.1"/></svg>
        asolera@telvano.es
      </li>
      <li class="contact__item">
        <svg class="contact__icon" viewBox="0 0 12 12"><circle cx="6" cy="6" r="5.2" fill="none" stroke="#c8102e" stroke-width="1.1"/><ellipse cx="6" cy="6" rx="2.2" ry="5.2" fill="none" stroke="#c8102e" stroke-width="1"/><path d="M.8 6h10.4" stroke="#c8102e" stroke-width="1"/></svg>
        www.telvano.es
      </li>
      <li class="contact__item">
        <span class="contact__dot"></span>
        adriansolera
      </li>
    </ul>
  </div>
</section>

</body>
</html>
```